Support People to improve their image and well-being by provided personalised advise

We need a design for business cards that could be used for production on plano press. We build a new business in our region for advising mostly women (also men though) on style embracing several aspects including fashion, style, self-confidence and ultimately your internal and external image. The business card should be "classy", "french-style". The business is located in the french -speaking part of Switzerland, close to France. The name of the company is Lomu Grace

Target Market(s)

Service fees won't be cheap (medium to premium) thus we target mid-class to upper-class women (1st target) and men (2nd target)

Industry/Entity Type

Life Coaching

Contact Information for Business Card

Conseil en Image

+41 76 418 63 07
tovasel@lomu-grace.example
linkedin.example/in/sel-moran-tova

Logo Text

Lomu Grace

Colors

Designer to choose colors to be used in the design.

```html
<!DOCTYPE html>
<html lang="fr">
<head>
<meta charset="utf-8">
<title>Lomu Grace – Business Cards</title>
<link href="https://fonts.googleapis.com/css2?family=Jost:wght@400;500&family=Caveat+Brush&display=swap" rel="stylesheet">
<style>
  :root {
    --backdrop: #acacac;
    --card-dark: #363b3f;
    --card-light: #f2f2f1;
    --gold: #c49a6c;
    --ink: #2f3336;
    --wordmark-light: #d9d9d9;
    --shadow: rgba(0, 0, 0, 0.22);
  }
  * { margin: 0; padding: 0; box-sizing: border-box; }
  html, body {
    width: 1200px;
    height: 576px;
    overflow: hidden;
    background: var(--backdrop);
    font-family: "Jost", sans-serif;
  }
  .stage { position: relative; width: 1200px; height: 576px; }

  .card {
    position: absolute;
    top: 138px;
    height: 293px;
    border-radius: 14px;
    box-shadow: 2px 3px 6px var(--shadow);
  }
  .card--front { left: 82px; width: 484px; background: var(--card-dark); }
  .card--back  { left: 602px; width: 481px; background: var(--card-light); }

  .brand-dot {
    position: absolute;
    width: 40px;
    height: 40px;
    border-radius: 50%;
    background: var(--gold);
  }
  .wordmark {
    position: absolute;
    font-weight: 400;
    letter-spacing: 0.16em;
    white-space: nowrap;
    text-transform: uppercase;
  }

  .card--front .brand-dot { left: 222px; top: 110px; }
  .card--front .wordmark {
    left: 0; width: 100%;
    top: 181px;
    text-align: center;
    font-size: 26px;
    color: var(--wordmark-light);
  }

  .person-name {
    position: absolute;
    left: 30px;
    top: 34px;
    font-family: "Caveat Brush", cursive;
    font-size: 25px;
    font-weight: 400;
    color: var(--gold);
    letter-spacing: 0.01em;
    white-space: nowrap;
  }
  .person-role {
    position: absolute;
    left: 30px;
    top: 69px;
    font-size: 12.5px;
    color: var(--ink);
  }

  .contact-list {
    position: absolute;
    left: 30px;
    top: 208px;
    list-style: none;
  }
  .contact-list li {
    display: flex;
    align-items: center;
    height: 17.5px;
    font-size: 13px;
    color: var(--ink);
    white-space: nowrap;
  }
  .contact-list svg { width: 11px; height: 11px; margin-right: 12px; fill: var(--ink); flex: none; }

  .card--back .brand-dot { left: 340px; top: 170px; }
  .card--back .wordmark {
    right: 30px;
    top: 233px;
    font-size: 24px;
    color: var(--ink);
  }
</style>
</head>
<body>
<main class="stage">
  <section class="card card--front" aria-label="Card front">
    <span class="brand-dot" aria-hidden="true"></span>
    <p class="wordmark">Lomu Grace</p>
  </section>

  <section class="card card--back" aria-label="Card back">
    <h1 class="person-name">Elise Marin Duval</h1>
    <p class="person-role">Conseil en Image</p>

    <ul class="contact-list">
      <li>
        <svg viewBox="0 0 12 12" aria-hidden="true"><path d="M1 3.5C1 2 2.5 1 6 1s5 1 5 2.5v1.2H8.2V3.6H3.8v1.1H1z M3 5.5h6l2 4.5v1H1v-1z M6 6.8a1.6 1.6 0 1 0 0 3.2a1.6 1.6 0 1 0 0-3.2z"/></svg>
        +41 00 000 00 00
      </li>
      <li>
        <svg viewBox="0 0 12 12" aria-hidden="true"><path d="M0.5 2.5h11v7h-11z M1.5 3.3v0.4L6 6.8l4.5-3.1v-0.4z" fill-rule="evenodd"/></svg>
        tovasel@lomu-grace.example
      </li>
      <li>
        <svg viewBox="0 0 12 12" aria-hidden="true"><path d="M6 0.8a5.2 5.2 0 1 0 0 10.4A5.2 5.2 0 1 0 6 0.8z M6 1.9c-0.7 0.8-1.1 2.2-1.2 3.6h2.4C7.1 4.1 6.7 2.7 6 1.9z M1.9 5.5h1.9c0.1-1.3 0.4-2.5 0.9-3.3A4.2 4.2 0 0 0 1.9 5.5z M8.2 5.5h1.9a4.2 4.2 0 0 0-2.8-3.3c0.5 0.8 0.8 2 0.9 3.3z M1.9 6.5a4.2 4.2 0 0 0 2.8 3.3c-0.5-0.8-0.8-2-0.9-3.3z M4.8 6.5c0.1 1.4 0.5 2.8 1.2 3.6c0.7-0.8 1.1-2.2 1.2-3.6z M8.2 6.5c-0.1 1.3-0.4 2.5-0.9 3.3a4.2 4.2 0 0 0 2.8-3.3z" fill-rule="evenodd"/></svg>
        www.lomu-grace.example
      </li>
    </ul>

    <span class="brand-dot" aria-hidden="true"></span>
    <p class="wordmark">Lomu Grace</p>
  </section>
</main>
</body>
</html>
```